Print materials for 3-star hotel

We are changing up our print materials (notepads, letterheads, key card jackets, small flyer for the room rates) We are a 3 star business hotel in the Philippines and have mainly used grey tones and clean, simple lines. See attached photos for logo and hotel interior photos.

Target Market(s)

Business

Contact Information for Business Card

Corvale Terrace Hotel
Lindwell Banca Avenue corner Tolenta St Cebu City 6000 Philippines
Tel: +63 32 481 7302
Mobile: +63 917 648 2095
www.corvaleterracehotel.example

Font styles to use
Serif
Sans Serif

Requirements
Must have
• Simple
• Readable font and font size
Nice to have
• Neutral colors, grey and taupes
Should not have
• No purples and bright blues

```html
<!DOCTYPE html>
<html lang="en">
<head>
<meta charset="utf-8">
<title>Corvale Terrace Hotel – Business Card</title>
<link rel="stylesheet" href="https://fonts.googleapis.com/css2?family=Open+Sans:wght@400;600;700&display=swap">
<style>
  :root {
    --backdrop: #3b332f;
    --card: #111111;
    --card-edge: #1c1c1c;
    --silver: #9a9a9a;
    --silver-soft: #7d7d7d;
    --white: #ffffff;
    --divider: #5a5a5a;
  }
  * { box-sizing: border-box; margin: 0; padding: 0; }
  html, body {
    width: 1200px; height: 864px; overflow: hidden;
    background: var(--backdrop);
    font-family: "Open Sans", Arial, sans-serif;
  }
  .sheet {
    position: relative; width: 1200px; height: 864px;
  }
  .card {
    position: absolute;
    width: 530px; height: 303px;
    background: var(--card);
    border: 1px solid var(--card-edge);
    box-shadow: 0 14px 30px rgba(0,0,0,.45);
  }
  .card--front { left: 45px; top: 280px; }
  .card--back { left: 625px; top: 280px; }

  /* Front */
  .front-brand {
    position: absolute; left: 0; right: 0; top: 92px;
    display: flex; flex-direction: column; align-items: center;
  }
  .front-brand__square {
    width: 40px; height: 40px; background: var(--silver); margin-bottom: 16px;
  }
  .front-brand__name {
    color: var(--silver); font-weight: 400;
    font-size: 20px; letter-spacing: 6px; text-transform: uppercase;
  }
  .front-brand__sub {
    color: var(--silver); font-weight: 400;
    font-size: 13px; letter-spacing: 8px; text-transform: uppercase; margin-top: 4px;
  }
  .front-web {
    position: absolute; left: 0; right: 0; bottom: 58px; text-align: center;
    color: var(--silver-soft); font-size: 12px; letter-spacing: 3px;
  }

  /* Back */
  .back-brand {
    position: absolute; left: 34px; top: 78px; width: 190px;
    display: flex; flex-direction: column; align-items: flex-start;
  }
  .back-brand__square {
    width: 62px; height: 62px; background: var(--white); margin-bottom: 14px;
  }
  .back-brand__name {
    color: var(--white); font-weight: 700; font-size: 21px; line-height: 1.2;
    text-transform: uppercase; letter-spacing: 1px;
  }
  .back-divider {
    position: absolute; left: 236px; top: 48px; width: 1px; height: 210px;
    background: linear-gradient(to bottom, transparent, var(--divider), transparent);
  }
  .contact {
    position: absolute; left: 256px; top: 60px; color: var(--white);
  }
  .contact__name { font-weight: 700; font-size: 17px; letter-spacing: .5px; }
  .contact__role { font-size: 12px; letter-spacing: 1px; margin-bottom: 6px; }
  .contact__address { font-size: 13px; line-height: 1.35; margin-bottom: 6px; }
  .contact__list { list-style: none; font-size: 13px; line-height: 1.45; }
  .contact__list li { display: flex; align-items: center; gap: 9px; }
  .contact__list svg { width: 12px; height: 12px; flex: none; fill: var(--white); }
</style>
</head>
<body>
<main class="sheet">
  <section class="card card--front">
    <div class="front-brand">
      <span class="front-brand__square"></span>
      <span class="front-brand__name">Corvale Terrace</span>
      <span class="front-brand__sub">Hotel</span>
    </div>
    <p class="front-web">www.corvaleterrace.example</p>
  </section>

  <section class="card card--back">
    <div class="back-brand">
      <span class="back-brand__square"></span>
      <span class="back-brand__name">Corvale<br>Terrace</span>
    </div>
    <div class="back-divider"></div>
    <div class="contact">
      <p class="contact__name">ELLIS MARROW</p>
      <p class="contact__role">PRESIDENT</p>
      <p class="contact__address">4127 Halden Crest Drive<br>Brookvale, NY 10482</p>
      <ul class="contact__list">
        <li><svg viewBox="0 0 12 12"><path d="M1 4c0-2 2-3 5-3s5 1 5 3l-2 1-1-2H4L3 5zM2 6h8l1 5H1z"/></svg>555 0148 2261</li>
        <li><svg viewBox="0 0 12 12"><path d="M3 0h6v12H3zM4 1.5v8h4v-8z"/></svg>555 0193 7410</li>
        <li><svg viewBox="0 0 12 12"><path d="M3 0h6v4H3zM1 4h10v6H1zM3 7h6v5H3z"/></svg>555 0127 6634</li>
        <li><svg viewBox="0 0 12 12"><path d="M0 2h12v8H0zM1 3l5 4 5-4v-.5H1z"/></svg>ellis@corvaleterrace.example</li>
        <li><svg viewBox="0 0 12 12"><circle cx="6" cy="6" r="6"/><path d="M3 4h6v1H3zM3 7h6v1H3z" fill="#111"/></svg>www.corvaleterrace.example</li>
      </ul>
    </div>
  </section>
</main>
</body>
</html>
```